Marlowby Services Website Design

We have most content but require a professional design. We have a logo already and will need it utilized along with several of the photos from the attached documentation.
First page should have our mission and Vision and the synapsis provided in the word document. Visitors will be prompted to select from one of our 3 divisions from this page.
Each division will have the same list of tabs : About, Services, Safety, Careers and Contact.
Photos on each divisions page should be representative of the divisions offerings. The word doc attached contains the requested content and we are open to edits that would complement and fill the website.
I like the Quorvane site www.quorvane.example - they are our competition so cant be modeled directly after this.
Please include prompts to request quote at each service page. align the format of the geotechnical page to the other 2 divisions.
I used chat gpt for some of the content so will need it optimized for SCO.

```html
<!DOCTYPE html>
<html lang="en">
<head>
<meta charset="utf-8">
<title>Marlowby Services</title>
<link href="https://fonts.googleapis.com/css2?family=Lato:wght@400;700&family=Michroma&display=swap" rel="stylesheet">
<style>
:root{
  --red:#ee1c25;
  --red-dark:#b5141b;
  --ink:#111111;
  --text:#555555;
  --white:#ffffff;
  --footer:#0b0b0b;
  --hero-a:#2a2d2e;
  --hero-b:#3d3f3c;
}
*{margin:0;padding:0;box-sizing:border-box}
html,body{width:1200px;height:2323px;overflow:hidden;background:var(--white)}
body{position:relative;font-family:"Lato",sans-serif;color:var(--ink)}
.display{font-family:"Michroma",sans-serif;text-transform:uppercase}
.abs{position:absolute}

.top-rule{left:0;top:0;width:1200px;height:4px;background:var(--red)}
.site-header{left:0;top:4px;width:1200px;height:93px;background:var(--white)}
.brand{left:112px;top:30px;font-family:"Michroma",sans-serif;font-size:30px;color:var(--red);letter-spacing:1px}
.main-nav{right:112px;top:40px;display:flex;gap:53px;font-size:17px}
.main-nav a{color:var(--ink);text-decoration:none}

.hero{left:0;top:97px;width:1200px;height:568px;background:linear-gradient(135deg,var(--hero-a),var(--hero-b) 55%,#2e302f)}
.hero-kicker{left:112px;top:228px;font-size:35px;color:var(--white);letter-spacing:3px}
.hero-brand{left:110px;top:286px;font-size:55px;color:var(--red);letter-spacing:2px}
.hero-copy{left:112px;top:375px;width:420px;font-size:15.5px;line-height:29.5px;color:var(--white)}
.btn{display:flex;align-items:center;justify-content:center;font-weight:700;font-size:17px;text-decoration:none}
.btn-red{background:var(--red);color:var(--white)}
.btn-white{background:var(--white);color:var(--red)}
.hero-contact{left:112px;top:486px;width:120px;height:43px}
.hero-start{left:258px;top:486px;width:120px;height:43px}
.play{left:900px;top:339px}

.division-band{left:0;top:665px;width:1200px;height:128px;background:var(--red);color:var(--white)}
.division-title{left:110px;top:31px;font-size:25px;line-height:38px;letter-spacing:2px}
.division-rule{left:332px;top:25px;width:1px;height:80px;background:rgba(255,255,255,.7)}
.division{top:28px;display:flex;flex-direction:column;gap:6px;font-size:20px}
.division svg{display:block}

.tab{top:875px;width:272px;height:59px;display:flex;align-items:center;justify-content:center;font-size:21px;font-weight:700;color:var(--red);background:var(--white);border-radius:3px}
.tab-vision{left:310px;box-shadow:0 3px 14px rgba(0,0,0,.08)}
.tab-mission{left:619px;border:2px solid var(--red)}

.mission-title{left:110px;top:1022px;font-size:37px;line-height:59px;letter-spacing:3px}
.mission-copy{left:111px;top:1141px;width:465px;font-size:15px;line-height:31px;color:var(--text)}
.mission-copy p+p{margin-top:31px}
.read-more{left:111px;top:1471px;width:120px;height:43px}
.mission-photo{left:600px;top:1003px;width:488px;height:535px;border-radius:28px;background:linear-gradient(180deg,#2f6fd6 0%,#5a93e8 50%,#c9c9c4 70%,#6f6f6b 100%);box-shadow:0 6px 24px rgba(0,0,0,.18)}

.services-title{left:0;top:1615px;width:1200px;text-align:center;font-size:35px;letter-spacing:3px}
.card{top:1700px;width:314px;height:466px;background:var(--white);border-radius:14px;box-shadow:0 2px 14px rgba(0,0,0,.08)}
.card-photo{position:absolute;left:7px;top:7px;width:300px;height:268px}
.card h3{position:absolute;left:0;top:300px;width:100%;text-align:center;font-size:23px;font-weight:400;color:var(--red)}
.card p{position:absolute;left:14px;top:336px;width:286px;text-align:center;font-size:15px;line-height:29px;color:var(--text)}
.card .btn{position:absolute;left:80px;top:445px;width:137px;height:42px;font-size:16px}
.arrow{top:1921px}

.site-footer{left:0;top:2258px;width:1200px;height:65px;background:var(--footer);color:var(--white);font-size:14px}
.site-footer span{position:absolute;top:23px}
.social{position:absolute;top:21px;width:20px;height:20px;border-radius:50%;background:var(--red)}
</style>
</head>
<body>
<div class="abs top-rule"></div>
<header class="abs site-header">
  <div class="abs brand">MARLOWBY</div>
  <nav class="abs main-nav">
    <a href="#">About Us</a><a href="#">Services</a><a href="#">Safety</a><a href="#">Careers</a><a href="#">Contact Us</a>
  </nav>
</header>

<section class="abs hero" role="img" aria-label="Aerial view of a small town with a company aerial lift raising a 'for hire' sign, darkened overlay">
</section>
<div class="abs display hero-kicker">Welcome to</div>
<div class="abs display hero-brand">Marlowby</div>
<p class="abs hero-copy">Through collaboration, integrity, and dedication, we aim to contribute to the success of our clients while maintaining the highest standards of quality and professionalism.</p>
<a class="abs btn btn-red hero-contact" href="#">Contact Us</a>
<a class="abs btn btn-white hero-start" href="#">Get Started</a>
<svg class="abs play" width="84" height="84" viewBox="0 0 84 84" aria-label="Play video">
  <circle cx="42" cy="42" r="42" fill="#ee1c25" opacity=".45"/>
  <circle cx="42" cy="42" r="31" fill="#ee1c25"/>
  <rect x="33" y="35" width="18" height="14" rx="3" fill="#fff"/>
  <path d="M40 38.5 L46 42 L40 45.5Z" fill="#ee1c25"/>
</svg>

<section class="abs division-band">
  <div class="abs display division-title">Select<br>Division</div>
  <div class="abs division-rule"></div>
  <div class="abs division" style="left:404px">
    <svg width="40" height="44" viewBox="0 0 40 44" fill="none" stroke="#fff" stroke-width="2"><path d="M20 6v26M12 16l8 -10 8 10"/><circle cx="20" cy="36" r="5"/><path d="M6 24h8M26 24h8M4 30h6M30 30h6"/></svg>
    <span>Aerial Access</span>
  </div>
  <div class="abs division" style="left:590px">
    <svg width="44" height="46" viewBox="0 0 44 46" fill="none" stroke="#fff" stroke-width="2"><circle cx="22" cy="26" r="14"/><circle cx="22" cy="26" r="6"/><path d="M22 2v14M16 6h12M8 26H2M42 26h-6"/></svg>
    <span>Geotechnical Drilling</span>
  </div>
  <div class="abs division" style="left:843px">
    <svg width="44" height="46" viewBox="0 0 44 46" fill="none" stroke="#fff" stroke-width="2"><path d="M22 8a12 12 0 0 0-7 22v5h14v-5a12 12 0 0 0-7-22z"/><path d="M17 40h10M22 30v-10M22 22l-4-4M22 22l4-4M22 1v3M6 8l3 3M38 8l-3 3M2 20h4M38 20h4"/></svg>
    <span>Renewable Energy Services</span>
  </div>
</section>

<div class="abs tab tab-vision">Our Vision</div>
<div class="abs tab tab-mission">Mission Statement</div>

<h2 class="abs display mission-title">Our Mission<br>Statement</h2>
<div class="abs mission-copy">
  <p>At Marlowby, our mission is to deliver unparalleled aerial access, geotechnical drilling, and service and maintenance solutions, consistently exceeding our clients' expectations. We strive to achieve this by investing in cutting-edge technology, fostering a culture of safety and continuous improvement, and prioritizing environmental sustainability.</p>
  <p>Through collaboration, integrity, and dedication, we aim to contribute to the success of our clients while maintaining the highest standards of quality and professionalism.</p>
</div>
<a class="abs btn btn-red read-more" href="#">Read More</a>
<div class="abs mission-photo" role="img" aria-label="White aerial lift truck parked in front of a water tower under a blue sky"></div>

<h2 class="abs display services-title">Our Marlowby Services</h2>

<svg class="abs arrow" style="left:47px" width="24" height="24" viewBox="0 0 24 24"><circle cx="12" cy="12" r="11" fill="#444"/><path d="M14 6l-6 6 6 6M8 12h10" stroke="#fff" stroke-width="2.4" fill="none"/></svg>
<svg class="abs arrow" style="left:1129px" width="24" height="24" viewBox="0 0 24 24"><circle cx="12" cy="12" r="11" fill="#444"/><path d="M10 6l6 6-6 6M16 12H6" stroke="#fff" stroke-width="2.4" fill="none"/></svg>

<article class="abs card" style="left:99px">
  <div class="card-photo" role="img" aria-label="Aerial lift truck parked on a gravel lot beside trees" style="background:linear-gradient(180deg,#3f5a3a,#7d8a6b 45%,#b8b1a2)"></div>
  <h3>Delivering Safe</h3>
  <p>On the other hand, we denounce with righteous indignation and dislike men who are so beguiled and demora</p>
  <a class="btn btn-red" href="#">View Details</a>
</article>
<article class="abs card" style="left:443px">
  <div class="card-photo" role="img" aria-label="Aerial view of a town with a lift boom raising a company sign" style="background:linear-gradient(180deg,#9aa08f,#7a7e72 50%,#8f8d86)"></div>
  <h3>Construction</h3>
  <p>On the other hand, we denounce with righteous indignation and dislike men who are so beguiled and demora</p>
  <a class="btn btn-red" href="#">View Details</a>
</article>
<article class="abs card" style="left:787px">
  <div class="card-photo" role="img" aria-label="Rooftops covered with solar panels across an industrial district" style="background:linear-gradient(180deg,#b9d3e8,#7f8fa3 40%,#3e4f6a)"></div>
  <h3>Renewable Energy Industries</h3>
  <p>On the other hand, we denounce with righteous indignation and dislike men who are so beguiled and demora</p>
  <a class="btn btn-red" href="#">View Details</a>
</article>

<footer class="abs site-footer">
  <span style="left:112px">(C) Copyright 2024 | All Rights Reserved</span>
  <span style="left:707px">Privacy Policy</span>
  <span style="left:822px">|</span>
  <span style="left:856px">Terms Of Conditions</span>
  <div class="social" style="left:1009px" aria-label="Social link"></div>
  <div class="social" style="left:1038px" aria-label="Social link"></div>
  <div class="social" style="left:1067px" aria-label="Social link"></div>
</footer>
</body>
</html>
```